Business IT Services Billboard to attract local small businesses

We are Brivoqua, a premier Managed Service Provider (MSP) specializing in comprehensive IT services and VOIP phone solutions exclusively for businesses. Our goal is to create a dynamic and visually engaging billboard advertisement that not only highlights our cutting-edge IT solutions but also emphasizes our state-of-the-art VOIP phone services. This billboard should communicate our commitment to providing innovative, reliable, and holistic technology solutions.
See the attached supporting documentation.
Target Market(s)
small business
Industry/Entity Type
Information Technology
Colors
Designer to choose colors to be used in the design.
Look and feel
Each slider illustrates characteristics of the customer's brand and the style your logo design should communicate.

```html
<!DOCTYPE html>
<html lang="en">
<head>
<meta charset="UTF-8">
<title>Brivoqua Billboard</title>
<link href="https://fonts.googleapis.com/css2?family=Anton&family=Open+Sans:wght@600;700&display=swap" rel="stylesheet">
<style>
  :root {
    --page-bg: #e6e7ea;
    --board-black: #050607;
    --tech-teal: #173f47;
    --tech-deep: #0a1c22;
    --accent-blue: #1f7fd1;
    --band-blue: #1b78c8;
    --text-white: #ffffff;
  }
  * { margin: 0; padding: 0; box-sizing: border-box; }
  html, body {
    width: 1200px;
    height: 1200px;
    overflow: hidden;
    background: var(--page-bg);
  }
  .canvas {
    position: relative;
    width: 1200px;
    height: 1200px;
    display: flex;
    align-items: center;
    justify-content: center;
  }
  .billboard {
    position: relative;
    width: 1120px;
    height: 380px;
    background: var(--board-black);
    overflow: hidden;
    font-family: "Open Sans", sans-serif;
    color: var(--text-white);
  }
  .tech-visual {
    position: absolute;
    top: 0;
    right: 0;
    width: 560px;
    height: 100%;
    background:
      radial-gradient(ellipse at 78% 35%, #2f6a70 0%, rgba(23,63,71,0.7) 30%, rgba(10,28,34,0) 70%),
      linear-gradient(90deg, var(--board-black) 0%, var(--tech-deep) 35%, var(--tech-teal) 100%);
  }
  .headline {
    position: absolute;
    left: 70px;
    top: 40px;
    font-family: "Anton", sans-serif;
    font-weight: 400;
    text-transform: uppercase;
    line-height: 1.1;
    letter-spacing: 0.5px;
  }
  .headline-line { display: block; white-space: nowrap; }
  .headline-line.first { font-size: 52px; padding-left: 84px; }
  .headline-line.second { font-size: 56px; }
  .subline {
    position: absolute;
    left: 90px;
    top: 186px;
    white-space: nowrap;
  }
  .subline-accent {
    font-size: 21px;
    font-weight: 700;
    color: var(--accent-blue);
    letter-spacing: 0.6px;
    text-transform: uppercase;
  }
  .subline-rest {
    font-size: 15px;
    font-weight: 600;
    color: var(--text-white);
  }
  .call-to-action {
    position: absolute;
    left: 140px;
    top: 252px;
    font-size: 31px;
    font-weight: 600;
    white-space: nowrap;
  }
  .web-band {
    position: absolute;
    right: 0;
    top: 292px;
    width: 470px;
    height: 58px;
    background: var(--band-blue);
    clip-path: polygon(22px 0, 100% 0, 100% 100%, 0 100%);
    display: flex;
    align-items: center;
    padding-left: 40px;
  }
  .web-address {
    font-size: 30px;
    font-weight: 700;
    color: var(--text-white);
    letter-spacing: 0.3px;
  }
  .brand-name {
    position: absolute;
    right: 60px;
    top: 118px;
    font-family: "Open Sans", sans-serif;
    font-weight: 700;
    font-size: 34px;
    line-height: 1;
    color: var(--text-white);
    white-space: nowrap;
  }
</style>
</head>
<body>
  <main class="canvas">
    <section class="billboard">
      <div class="tech-visual" role="img" aria-label="Hand touching a glowing digital network of connected points"></div>
      <h1 class="headline">
        <span class="headline-line first">Seamless Technology</span>
        <span class="headline-line second">Solutions for Modern Businesses</span>
      </h1>
      <p class="subline">
        <span class="subline-accent">Innovative IT and VOIP Solutions</span>
        <span class="subline-rest">Tailored for Your Business Success</span>
      </p>
      <p class="call-to-action">Transform Your Tech Today</p>
      <div class="brand-name">Brivoqua</div>
      <div class="web-band">
        <span class="web-address">www.brivoqua.com</span>
      </div>
    </section>
  </main>
</body>
</html>
```